CANNABIS BASED BUSINESS CARD DESIGN AND CREATION

WE ARE A PRIVATELY OWNED INVESTMENT CORPORATION. WE PRIMARILY INVEST IN LEGAL PUBLICALLY TRADED CANNABIS COMPANIES THAT ARE TRADED THROUGH THE OTC OR VOLTRIX. WE OFFER THE PUBLIC AN OPPORTUNITY TO PARTICIPATE DIRECTLY WITH THESE COMPANIES FOR NO FEES, NO COMMISSIONS AND IN DEPTH RESEARCH ON EVERY COMPANY PROFILE. WE ARE ALSO PRO FEDERAL LEGALIZATION AND WILL APPLY FOR CULTIVATION AND DISPENSARY LICENSES WHEN THEY BECOME AVAILABLE.

Target Market(s)

30-60 FEMALE AND MALE INVESTORS

Industry/Entity Type

Business

Contact Information for Business Card

EDS CAPITAL GROUP CORPERIN D SLAUGHTER(469) 426-6302ERIN@EDSCAPITALGROUP.COM

Font styles to use
Decorative

Requirements
Must have
• COMPANY LOGO
• CANNABIS LOGO
Nice to have
• MODERN FONT AND LOGOS

```html
<!DOCTYPE html>
<html lang="en">
<head>
<meta charset="utf-8">
<title>TQM Capital Group Corp – Business Card</title>
<link rel="stylesheet" href="https://fonts.googleapis.com/css2?family=Lato:wght@400;700&display=swap">
<style>
  :root {
    --stage: #262626;
    --card-dark-top: #3a3637;
    --card-dark-bottom: #131213;
    --card-green-top: #c8d530;
    --card-green-bottom: #8fae3c;
    --ink-black: #111111;
    --ink-white: #ffffff;
    --leaf-shadow: rgba(0, 0, 0, 0.35);
  }
  * { box-sizing: border-box; margin: 0; padding: 0; }
  html, body {
    width: 1200px; height: 900px; overflow: hidden;
    background: var(--stage);
    font-family: "Lato", sans-serif;
  }
  .canvas { position: relative; width: 1200px; height: 900px; }
  .card {
    position: absolute; left: 282px;
    width: 636px; height: 360px;
    border-radius: 20px; overflow: hidden;
    box-shadow: 0 12px 30px rgba(0, 0, 0, 0.45);
  }
  .card-back {
    top: 75px;
    background: linear-gradient(160deg, var(--card-dark-top) 0%, var(--card-dark-bottom) 75%);
  }
  .leaf-decoration {
    position: absolute; right: 20px; top: 40px;
    width: 250px; height: 260px; border-radius: 50%;
    background: radial-gradient(circle at 50% 50%, var(--leaf-shadow) 0%, rgba(0,0,0,0.15) 45%, rgba(0,0,0,0) 70%);
  }
  .company-name {
    position: absolute; left: 0; right: 0;
    display: flex; justify-content: center; align-items: center; gap: 12px;
    font-size: 28px; font-weight: 700; letter-spacing: 0.5px;
    white-space: nowrap;
  }
  .company-dot {
    width: 14px; height: 14px; border-radius: 50%;
    background: currentColor;
  }
  .card-back .company-name { top: 150px; color: var(--ink-white); }
  .card-front {
    top: 465px;
    background: linear-gradient(180deg, var(--card-green-top) 0%, var(--card-green-bottom) 100%);
  }
  .card-front .company-name { top: 110px; color: var(--ink-black); }
  .contact-list {
    position: absolute; left: 80px; top: 252px;
    list-style: none; color: var(--ink-white); font-size: 13px;
  }
  .contact-list li {
    display: flex; align-items: center; gap: 12px; height: 22.5px;
  }
  .contact-list svg { width: 14px; height: 14px; fill: var(--ink-white); }
  .holder-name {
    position: absolute; left: 383px; top: 250px;
    color: var(--ink-white); font-size: 22px; font-weight: 700;
  }
</style>
</head>
<body>
<main class="canvas">
  <section class="card card-back">
    <div class="leaf-decoration" role="img" aria-label="Faint cannabis leaf decoration"></div>
    <p class="company-name"><span class="company-dot" aria-hidden="true"></span>TQM Capital Group Corp</p>
  </section>

  <section class="card card-front">
    <p class="company-name"><span class="company-dot" aria-hidden="true"></span>TQM Capital Group Corp</p>
    <ul class="contact-list">
      <li>
        <svg viewBox="0 0 16 16" aria-hidden="true"><path d="M3 2h3l1.5 3.5-2 1.3a8 8 0 0 0 3.7 3.7l1.3-2L14 10v3a1 1 0 0 1-1 1A11 11 0 0 1 2 3a1 1 0 0 1 1-1z"/></svg>
        <span>(555) 013-4478</span>
      </li>
      <li>
        <svg viewBox="0 0 16 16" aria-hidden="true"><path d="M1 3h14v10H1z M1.8 3.8 8 8.8l6.2-5H1.8z" fill-rule="evenodd"/></svg>
        <span>marla@tqmcapitalgroup-demo.com</span>
      </li>
      <li>
        <svg viewBox="0 0 16 16" aria-hidden="true"><path d="M6.5 9.5l3-3M7 4.5l1.5-1.5a2.8 2.8 0 0 1 4 4L11 8.5M9 11.5 7.5 13a2.8 2.8 0 0 1-4-4L5 7.5" fill="none" stroke="#fff" stroke-width="1.6" stroke-linecap="round"/></svg>
        <span>www.tqmcapitalgroup-demo.com</span>
      </li>
    </ul>
    <p class="holder-name">Marla J Pendlebury</p>
  </section>
</main>
</body>
</html>
```